CM Candle Tube Packaging Design

Website: www.corvelmare.example
IG: @corvel.mare
Tagline: Elevate Your Ambiance
My brand is a sophisticated brand with luxury candles made of coconut wax. Im looking for an upscale minimalist chic design.
Discover the transformative power of positive energy with Corvel Mare candles. Indulge in true luxury with our specially crafted coconut wax blend that not only ignites captivating scents but also embodies modern elegance and empowering elements.
At Corvel Mare we're committed to delivering a unique and exhilarating aromatic experience to all candle lovers. Each candle is meticulously handcrafted in small batches using luxury fragrance oils exclusively formulated for coconut wax.
Our candles are:
Clean-burning
Paraben-Free
Phthalate-Free
Skin-Safe
Pet-Friendly

```html
<!DOCTYPE html>
<html lang="en">
<head>
<meta charset="UTF-8">
<title>Corvel Mare — Candle Label</title>
<link href="https://fonts.googleapis.com/css2?family=Italiana&family=Bodoni+Moda:wght@500&family=Allura&family=Poppins:wght@300;400&display=swap" rel="stylesheet">
<style>
  :root {
    --backdrop: #434f44;
    --label: #ffffff;
    --ink: #14161c;
    --sage: #8f968f;
    --rule: #b9b9b9;
  }
  html, body {
    margin: 0;
    padding: 0;
    width: 1200px;
    height: 2824px;
    overflow: hidden;
    background: var(--backdrop);
  }
  .label {
    position: absolute;
    left: 80px;
    top: 567px;
    width: 1040px;
    height: 1690px;
    background: var(--label);
    box-shadow: 0 10px 40px rgba(0,0,0,0.25);
    color: var(--ink);
    text-align: center;
  }
  .label > * { position: absolute; left: 0; right: 0; margin: 0; }
  .brand-name {
    top: 300px;
    font-family: "Italiana", serif;
    font-size: 76px;
    letter-spacing: 2px;
    line-height: 1;
    display: flex;
    justify-content: center;
    align-items: center;
    gap: 22px;
  }
  .brand-dot {
    width: 12px; height: 12px;
    border-radius: 50%;
    background: var(--ink);
    display: inline-block;
  }
  .brand-sub {
    top: 420px;
    font-family: "Poppins", sans-serif;
    font-weight: 300;
    font-size: 23px;
    letter-spacing: 10px;
    display: flex;
    justify-content: center;
    align-items: center;
    gap: 26px;
  }
  .brand-sub::before, .brand-sub::after {
    content: "";
    width: 52px;
    height: 2px;
    background: var(--ink);
  }
  .brand-tag {
    top: 462px;
    font-family: "Allura", cursive;
    font-size: 26px;
    color: #555;
  }
  .headline {
    top: 535px;
    font-family: "Bodoni Moda", serif;
    font-weight: 500;
    font-size: 122px;
    line-height: 100px;
  }
  .headline-script {
    top: 720px;
    font-family: "Allura", cursive;
    font-size: 150px;
    line-height: 1;
    color: var(--sage);
  }
  .benefits {
    top: 858px;
    left: 258px;
    right: 258px;
    padding: 0;
    list-style: none;
    font-family: "Poppins", sans-serif;
    font-size: 21px;
  }
  .benefits li {
    height: 49.5px;
    line-height: 46px;
    border-bottom: 1.5px solid var(--rule);
  }
  .benefits li:last-child { border-bottom: none; }
  .product-type {
    top: 1123px;
    font-family: "Poppins", sans-serif;
    font-size: 25px;
    letter-spacing: 6px;
  }
  .product-size {
    top: 1166px;
    font-family: "Poppins", sans-serif;
    font-size: 26px;
  }
  .closing-rule {
    top: 1230px;
    display: flex;
    justify-content: center;
    align-items: center;
    gap: 40px;
  }
  .closing-rule .line {
    width: 188px;
    height: 2px;
    background: var(--ink);
  }
  .closing-rule .mark {
    width: 18px; height: 18px;
    border-radius: 50%;
    background: var(--ink);
  }
</style>
</head>
<body>
  <main class="label">
    <h1 class="brand-name">CORVEL<span class="brand-dot"></span>MARE</h1>
    <p class="brand-sub">HANDMADE CANDLES</p>
    <p class="brand-tag">with purpose and love</p>
    <h2 class="headline">Elevate<br>Your</h2>
    <p class="headline-script">Ambiance</p>
    <ul class="benefits">
      <li>CLEAN-BURNING</li>
      <li>PARABEN-FREE</li>
      <li>PHTHALATE-FREE</li>
      <li>SKIN-SAFE</li>
      <li>PET-FRIENDLY</li>
    </ul>
    <p class="product-type">COCONUT WAX CANDLE</p>
    <p class="product-size">14 oz (596 gm)</p>
    <div class="closing-rule"><span class="line"></span><span class="mark"></span><span class="line"></span></div>
  </main>
</body>
</html>
```